Design a refer a friend Flyer (French & English)
Flyer Title:
Main Title: "Refer a Friend & Receive a Free Electric Toothbrush!"
Bold and clear, centered at the top.
Use a clean and modern font.
Color: White text on a vivid green background for maximum contrast and readability.
Visual Focus:
Toothbrush Image: Place a high-quality image of the Dentiva Max 300 Electric Toothbrush in the center of the flyer.
Include a small price tag with “Value of $50” near the toothbrush to highlight the reward.
Simple Message:
Text: "Refer a friend to Centre Dentaire Lac-Ombré. When they book and attend their appointment, you get a free electric toothbrush, and they receive a special gift!"
Straightforward and easy to understand.
Placed below the image of the toothbrush.
Referral Process:
3 Easy Steps:
Refer a Friend
They Book and Come to Their Appointment
Receive Your Free Electric Toothbrush
Use simple, minimal icons to visually represent each step.
Keep the steps aligned horizontally or vertically for clarity.
Call to Action:
Text: "Start Referring Today!"
Place it in a button-like design in the vivid green color with bold, white text to make it stand out.
Contact Information:
Details:
Logo of Centre Dentaire Lac-Ombré.
Address: "42 Rue Valmonde Ouest, Suite 310".
Phone Number and Website: Positioned at the bottom for easy reference.
Color Scheme:
Use a vivid green background for the entire flyer, with white accents for text and icons to maintain a fresh, clean look.
Minimal clutter, focusing on clarity and the key elements: the toothbrush, the call to action, and contact information.
Clinic : www.cdlacombre.example
Attached is the brandbook, logo and inspo I made with AI.
French text will be provided.
Thank you,
Tarin

```html
<!DOCTYPE html>
<html lang="en">
<head>
<meta charset="utf-8">
<title>Refer a Friend Flyer – Clinique Dentaire Lac-Ombré</title>
<link href="https://fonts.googleapis.com/css2?family=Archivo+Black&family=Montserrat:wght@500;600;700;800&display=swap" rel="stylesheet">
<style>
  :root {
    --green: #17a86a;
    --green-light: #2cc47f;
    --navy: #111736;
    --white: #ffffff;
    --canvas: #e8ebe9;
  }
  * { box-sizing: border-box; margin: 0; padding: 0; }
  html, body { width: 1200px; height: 800px; overflow: hidden; }
  body {
    background: var(--canvas);
    font-family: "Montserrat", Arial, sans-serif;
    display: flex; align-items: center; justify-content: center;
  }
  .flyer {
    position: relative;
    width: 540px; height: 760px;
    background: var(--green);
    overflow: hidden;
    box-shadow: 0 6px 24px rgba(0,0,0,.15);
  }
  .footer-band {
    position: absolute; left: 0; right: 0; bottom: 0; height: 150px;
    background: var(--navy);
  }
  .headline {
    position: absolute; left: 36px; top: 56px; width: 340px;
    font-family: "Archivo Black", Impact, sans-serif;
    font-size: 30px; line-height: 1.05; color: var(--white);
    text-transform: uppercase; letter-spacing: -0.5px;
  }
  .product-visual {
    position: absolute; left: 398px; top: 34px; width: 78px; height: 606px;
    border-radius: 40px 40px 24px 24px;
    background: linear-gradient(180deg, #7ee8a4 0%, #e9eef2 7%, #f2f4f5 24%, #1d1f22 29%, #2a2c30 70%, #121316 82%, #eceff1 86%, #d6dadd 100%);
    z-index: 2;
  }
  .value-badge {
    position: absolute; left: 276px; top: 262px; width: 132px; height: 132px;
    border-radius: 50%; background: var(--navy);
    border: 4px solid var(--navy);
    box-shadow: inset 0 0 0 5px var(--green-light);
    display: flex; flex-direction: column; align-items: center; justify-content: center;
    color: var(--white); font-family: "Archivo Black", Impact, sans-serif;
    text-transform: uppercase; z-index: 1;
  }
  .value-badge .label { font-size: 14px; }
  .value-badge .amount { font-size: 42px; line-height: 1; }
  .process {
    position: absolute; left: 36px; top: 208px;
    font-family: "Archivo Black", Impact, sans-serif; text-transform: uppercase;
  }
  .process .title { font-size: 20px; color: var(--navy); }
  .process .subtitle { font-size: 15px; color: var(--white); margin-top: 2px; }
  .steps { position: absolute; left: 36px; top: 272px; list-style: none; }
  .step { display: flex; align-items: center; gap: 12px; height: 60px; }
  .step-icon {
    width: 46px; height: 46px; border-radius: 50%;
    background: var(--navy); border: 2px solid var(--green-light);
    display: flex; align-items: center; justify-content: center; flex: none;
  }
  .step-text { color: var(--white); font-size: 14px; font-weight: 600; line-height: 1.2; width: 170px; }
  .message {
    position: absolute; left: 36px; top: 470px; width: 330px;
    color: var(--white); font-size: 12.5px; font-weight: 500; line-height: 1.45;
  }
  .cta {
    position: absolute; left: 36px; top: 560px;
    color: var(--white); font-family: "Archivo Black", Impact, sans-serif;
    font-size: 16px; text-transform: uppercase;
  }
  .contact { position: absolute; left: 36px; top: 634px; color: var(--white); }
  .contact .heading {
    font-family: "Archivo Black", Impact, sans-serif; font-size: 14px;
    color: var(--green-light); text-transform: uppercase;
    border-bottom: 2px solid var(--green-light); padding-bottom: 3px; margin-bottom: 8px;
    display: inline-block;
  }
  .contact ul { list-style: none; }
  .contact li { display: flex; align-items: center; gap: 8px; font-size: 13px; font-weight: 600; height: 22px; }
  .contact .dot {
    width: 15px; height: 15px; border-radius: 50%; background: var(--green-light);
    display: flex; align-items: center; justify-content: center; flex: none;
  }
  .clinic-name {
    position: absolute; right: 30px; bottom: 34px;
    display: flex; align-items: center; gap: 10px; color: var(--white);
  }
  .clinic-name .mark { width: 30px; height: 30px; border-radius: 50%; background: var(--white); }
  .clinic-name .name { font-size: 20px; font-weight: 700; line-height: 1.1; }
  .clinic-name .name small { display: block; font-size: 10px; font-weight: 700; }
</style>
</head>
<body>
  <main class="flyer">
    <div class="footer-band"></div>

    <h1 class="headline">Refer a<br>friend &amp; receive<br>a free electric<br>toothbrush!</h1>

    <div class="value-badge">
      <span class="label">Value of</span>
      <span class="amount">$50</span>
    </div>

    <div class="product-visual" role="img" aria-label="Photo of the Dentiva Max 300 electric toothbrush standing on its charging base, with a green glow ring around the brush head"></div>

    <div class="process">
      <p class="title">Referral process:</p>
      <p class="subtitle">3 easy steps:</p>
    </div>

    <ol class="steps">
      <li class="step">
        <span class="step-icon">
          <svg width="24" height="24" viewBox="0 0 24 24" fill="none" stroke="#2cc47f" stroke-width="1.6">
            <circle cx="8" cy="8" r="3"/><circle cx="16" cy="8" r="3"/>
            <path d="M2 19c0-3.5 2.7-5.5 6-5.5s6 2 6 5.5M10 19c0-3.5 2.7-5.5 6-5.5s6 2 6 5.5"/>
          </svg>
        </span>
        <span class="step-text">Refer a Friend</span>
      </li>
      <li class="step">
        <span class="step-icon">
          <svg width="24" height="24" viewBox="0 0 24 24" fill="none" stroke="#2cc47f" stroke-width="1.6">
            <rect x="3" y="5" width="18" height="16" rx="2"/><path d="M3 10h18M8 3v4M16 3v4"/>
            <path d="M9 15l2 2 4-4"/>
          </svg>
        </span>
        <span class="step-text">They Book and Come to Their Appointment</span>
      </li>
      <li class="step">
        <span class="step-icon">
          <svg width="24" height="24" viewBox="0 0 24 24" fill="none" stroke="#2cc47f" stroke-width="1.6">
            <rect x="9" y="9" width="6" height="13" rx="2"/><path d="M11 9V3h2v6"/><path d="M10.5 3h3"/>
            <circle cx="12" cy="14" r="1"/>
          </svg>
        </span>
        <span class="step-text">Receive Your Free Electric Toothbrush</span>
      </li>
    </ol>

    <p class="message">Refer a friend to Centre Dentaire Lac-Ombré. When they book &amp; attend their appointment, you get a free electric toothbrush, and they receive a special gift!</p>

    <p class="cta">Start referring today!</p>

    <section class="contact">
      <p class="heading">Contact information:</p>
      <ul>
        <li><span class="dot"><svg width="9" height="9" viewBox="0 0 24 24" fill="#111736"><path d="M12 2a7 7 0 0 0-7 7c0 5 7 13 7 13s7-8 7-13a7 7 0 0 0-7-7zm0 9.5A2.5 2.5 0 1 1 12 6.5a2.5 2.5 0 0 1 0 5z"/></svg></span>42 Rue Valmonde Ouest, Suite 310</li>
        <li><span class="dot"><svg width="9" height="9" viewBox="0 0 24 24" fill="#111736"><path d="M6.6 10.8a15 15 0 0 0 6.6 6.6l2.2-2.2a1 1 0 0 1 1-.25 11.4 11.4 0 0 0 3.6.57 1 1 0 0 1 1 1V20a1 1 0 0 1-1 1A17 17 0 0 1 3 4a1 1 0 0 1 1-1h3.5a1 1 0 0 1 1 1 11.4 11.4 0 0 0 .57 3.6 1 1 0 0 1-.25 1z"/></svg></span>514-555-0172</li>
        <li><span class="dot"><svg width="9" height="9" viewBox="0 0 24 24" fill="none" stroke="#111736" stroke-width="2.5"><circle cx="12" cy="12" r="9"/><path d="M3 12h18M12 3c3 3.5 3 14.5 0 18M12 3c-3 3.5-3 14.5 0 18"/></svg></span>www.cdlacombre.example</li>
      </ul>
    </section>

    <div class="clinic-name">
      <span class="name">Clinique Dentaire<small>Lac-Ombré</small></span>
      <span class="mark"></span>
    </div>
  </main>
</body>
</html>
```